Varsity Purse Wordpress Website (re)design

we are a student run financial literacy website and are desperately trying to get college students to pay attention to the finances to create solid financial skills for life. This age group LOVES pixolette so instead of sharing a lot of text we want to tease through graphics/infographics topics that are relevant to them based on what their peers are discussing and then push them to our resources to learn more. ultimately we will also recommend products to them that are carefully selected by us. these will range from a book on paying back their student loan to a place to store their dorm stuff when they go home for summer break to a credit card we determine is best for them. So yes, commerce is imp but SEO to attract students comes first which we will do through survey monkey and cash prizes. we need to capture email address. we also have a "checklist" (attached and needs rebranding) of the basic and most imp money matters for them. Each item will hyperlink to our parnter, nuvoe, and need to do so seamlessly and push them back to us.

Target Market(s)

college students and young adults

Requirements
Must have
• simple, clean and graphic with an integration of survey monkey, an borvel store and a capture of emails through mailchimp or other similar. Ability to edit after ourselves on wordpress

```html
<!DOCTYPE html>
<html lang="en">
<head>
<meta charset="utf-8">
<title>Varsity Purse — Take Charge Of Your Change</title>
<link rel="stylesheet" href="https://fonts.googleapis.com/css2?family=Lora:ital,wght@0,400;0,600;1,600&family=Montserrat:wght@400;500&family=Ubuntu:wght@400;500;700&family=Playball&display=swap">
<style>
:root{
  --blue:#17659f;
  --green:#5cb531;
  --ink:#1d2430;
  --text:#333;
  --grey:#efefef;
  --white:#fff;
  --black:#000;
}
*{margin:0;padding:0;box-sizing:border-box}
html,body{width:1200px;height:2938px;overflow:hidden}
body{position:relative;background:var(--white);font-family:'Montserrat',sans-serif;color:var(--text)}
.abs{position:absolute}
a{color:inherit;text-decoration:none}

/* header */
.site-header{left:0;top:0;width:1200px;height:104px;background:var(--white)}
.brand{left:145px;top:22px;display:flex;align-items:center;gap:12px}
.brand-name{font-family:'Ubuntu',sans-serif;font-weight:500;font-size:40px;line-height:60px;color:var(--blue)}
.brand-dot{width:26px;height:26px;border-radius:50%;background:var(--green)}
.call{left:586px;top:36px;display:flex;align-items:center;gap:12px;font-family:'Montserrat',sans-serif;font-size:19px;color:#222}
.call-icon{width:35px;height:35px;border-radius:5px;background:var(--blue);display:flex;align-items:center;justify-content:center}
.call b{font-weight:500}
.call span{color:var(--blue)}
.btn{display:flex;align-items:center;justify-content:center;font-family:'Ubuntu',sans-serif;font-weight:500;text-transform:uppercase}
.quote-btn{left:864px;top:33px;width:188px;height:41px;background:var(--green);color:var(--white);font-size:14px}

.main-nav{left:0;top:104px;width:1200px;height:64px;background:var(--blue)}
.nav-list{list-style:none;display:flex;justify-content:center;gap:39px;height:100%;align-items:center;font-family:'Lora',serif;font-size:14px;letter-spacing:.3px;color:var(--white);text-transform:uppercase}

/* hero */
.hero{left:0;top:168px;width:1200px;height:559px;background:linear-gradient(180deg,#7f9a6a 0%,#a89b7c 45%,#6d5a4c 80%,#4b3a2f 100%)}
.hero-title{left:0;top:233px;width:1200px;text-align:center;font-family:'Lora',serif;font-weight:600;font-size:56px;color:var(--white);text-shadow:0 2px 6px rgba(0,0,0,.45)}
.hero-sub{left:255px;top:311px;width:690px;text-align:center;font-size:16.5px;line-height:27px;color:var(--white);text-shadow:0 1px 4px rgba(0,0,0,.55)}
.dot{border-radius:50%;background:var(--white)}

/* feature steps */
.step-badge{width:122px;height:122px;border-radius:50%;background:var(--white);box-shadow:0 3px 8px rgba(0,0,0,.2);display:flex;align-items:center;justify-content:center}
.step-num{width:80px;height:80px;border-radius:50%;background:var(--ink);color:var(--white);display:flex;align-items:center;justify-content:center;font-family:'Lora',serif;font-style:italic;font-weight:600;font-size:44px}
.step-num.is-green{background:var(--green)}
.step{width:270px;text-align:center}
.step h3{font-family:'Ubuntu',sans-serif;font-weight:400;font-size:25px;line-height:32px;color:#222;margin-bottom:18px}
.step h3.is-green{color:var(--green)}
.step p{font-size:16px;line-height:27px;color:#333}

/* about */
.about{left:0;top:1075px;width:1200px;height:535px;background:var(--grey)}
.photo-circle{border-radius:50%}
.about-eyebrow{left:599px;top:1137px;font-size:17px;color:#222}
.about-title{left:599px;top:1168px;font-family:'Ubuntu',sans-serif;font-weight:500;font-size:37px;color:#111}
.about-copy{left:602px;top:1226px;width:450px;font-size:13.6px;line-height:24px;color:#333}
.about-copy p{margin-bottom:8px}
.green-btn{background:var(--green);color:var(--white);font-size:15px}

/* course */
.course{left:0;top:1610px;width:1200px;height:566px;background:var(--blue)}
.course-title{left:145px;top:1703px;font-family:'Ubuntu',sans-serif;font-weight:700;font-size:38px;line-height:42px;color:var(--white)}
.course-copy{left:145px;top:1817px;width:490px;font-family:'Ubuntu',sans-serif;font-size:15.6px;line-height:29px;color:var(--white)}
.course-copy p{margin-bottom:12px}
.white-btn{background:var(--white);color:var(--blue);font-size:15px}
.checklist-card{left:666px;top:1656px;width:451px;height:473px;background:var(--white)}
.checklist-art{left:740px;top:1684px;width:303px;height:416px;background:linear-gradient(180deg,#e8f2fb 0%,#bfe0f5 20%,#a9d6f2 80%,#e8f2fb 100%)}

/* testimonials */
.reviews{left:0;top:2176px;width:1200px;height:548px;background:var(--grey)}
.reviews-title{left:0;top:2248px;width:1200px;text-align:center;font-family:'Ubuntu',sans-serif;font-size:42px;color:var(--blue)}
.avatar{width:94px;height:94px;border-radius:50%;background:linear-gradient(160deg,#d9b79a,#8a6a55)}
.avatar.is-active{border:4px solid var(--blue)}
.review-quote{left:240px;top:2490px;width:720px;text-align:center;font-size:16.5px;line-height:29px;color:#333}
.review-author{left:0;top:2592px;width:1200px;text-align:center;font-family:'Playball',cursive;font-size:27px;color:var(--blue)}

/* footer */
.site-footer{left:0;top:2724px;width:1200px;height:214px;background:var(--black)}
.social{left:446px;top:2760px;width:314px;height:58px;background:#0c0c0c;display:flex;justify-content:center;align-items:center;gap:14px}
.social-link{width:43px;height:43px;border-radius:50%;background:#1f1f1f;display:flex;align-items:center;justify-content:center}
.social-link i{display:block;width:10px;height:10px;border-radius:50%;background:var(--white)}
.footer-nav{left:0;top:2840px;width:1200px;height:28px}
.copyright{left:0;top:2886px;width:1200px;text-align:center;font-family:'Lora',serif;font-size:14px;color:var(--white)}
</style>
</head>
<body>

<header class="site-header abs">
  <a class="brand abs" href="#"><span class="brand-name">Varsity Purse</span><span class="brand-dot"></span></a>
  <div class="call abs">
    <span class="call-icon">
      <svg width="18" height="18" viewBox="0 0 24 24"><path fill="#fff" d="M6.6 10.8a15.1 15.1 0 0 0 6.6 6.6l2.2-2.2a1 1 0 0 1 1-.25 11.4 11.4 0 0 0 3.6.57 1 1 0 0 1 1 1V20a1 1 0 0 1-1 1A17 17 0 0 1 3 4a1 1 0 0 1 1-1h3.5a1 1 0 0 1 1 1c0 1.25.2 2.46.57 3.6a1 1 0 0 1-.25 1z"/></svg>
    </span>
    <b>Call Us:</b> <span>555-014-2290</span>
  </div>
  <a class="quote-btn btn abs" href="#">Request a quote</a>
</header>

<nav class="main-nav abs">
  <ul class="nav-list">
    <li>Home</li><li>Take the pledge</li><li>Blog</li><li>About us</li><li>Tips &amp; tricks</li><li>About nuvoe</li><li>Login</li>
  </ul>
</nav>

<section class="hero abs" role="img" aria-label="Photo of a group of smiling college students sitting together with laptops and tablets outdoors under trees"></section>
<h1 class="hero-title abs">Take Charge Of Your Change</h1>
<p class="hero-sub abs">To provide a comprehensive resource that enables college students and young adults to gain a better understanding of financial issues that will help them succeed in their careers and in life.</p>
<div class="abs" style="left:1121px;top:410px;width:26px;height:26px;border-radius:50%;border:2px solid #fff"></div>
<div class="dot abs" style="left:1127px;top:416px;width:14px;height:14px"></div>
<div class="dot abs" style="left:1127px;top:448px;width:13px;height:13px"></div>
<div class="dot abs" style="left:1127px;top:474px;width:13px;height:13px"></div>

<div class="step-badge abs" style="left:206px;top:666px"><span class="step-num">1</span></div>
<div class="step-badge abs" style="left:530px;top:666px"><span class="step-num is-green">2</span></div>
<div class="step-badge abs" style="left:846px;top:666px"><span class="step-num">3</span></div>

<article class="step abs" style="left:143px;top:824px">
  <h3>How To Budget</h3>
  <p>Having a solid budget is a fundamental building block in becoming financially independent,</p>
</article>
<article class="step abs" style="left:465px;top:808px">
  <h3 class="is-green">Money Saving Hacks<br>For Millennials</h3>
  <p>The other generations love to pick on us, but the unemployment rate is the lowest it’s been in over 50 years, so it’s good to be a millennial!</p>
</article>
<article class="step abs" style="left:787px;top:808px">
  <h3>How To Create Your<br>Own Side Hustle</h3>
  <p>So, you’re thinking of starting a side hustle, but before you do you should think about a few things.</p>
</article>

<section class="about abs"></section>
<div class="photo-circle abs" style="left:154px;top:1145px;width:296px;height:296px;background:linear-gradient(180deg,#7fb0d8 0%,#b6cfe2 50%,#3f8aa8 75%,#263a4a 100%)" role="img" aria-label="Photo of two friends on a car holding up colourful balloons against the sky"></div>
<div class="photo-circle abs" style="left:342px;top:1313px;width:212px;height:212px;border:6px solid #fff;background:linear-gradient(135deg,#4a4a4a 0%,#c9a98a 50%,#2d5fae 65%,#e8ddd0 100%)" role="img" aria-label="Photo of a hand passing a payment card to another hand"></div>
<p class="about-eyebrow abs">About Us</p>
<h2 class="about-title abs">Varsity Purse</h2>
<div class="about-copy abs">
  <p>Welcome to your FREE resource that will help you achieve financial independence and knowledge.</p>
  <p>Using peer-to-peer tips, personal stories and nuvoe, you can become a Varsity Purse!</p>
  <p>We promise to educate ourselves to gain financial independence. We are ready to work hard for it but want it to be fun. We won’t always depend on our parents. We won’t repeat the mistakes of our parent’s generation. We know that with financial independence we can achieve freedom. It’s time for us to take charge of our change. We’re next to run this world!</p>
</div>
<a class="green-btn btn abs" href="#" style="left:604px;top:1500px;width:145px;height:47px">Read more</a>

<section class="course abs"></section>
<h2 class="course-title abs">Why Take A Personal<br>Finance Course?</h2>
<div class="course-copy abs">
  <p>Varsity Purse will teach you how to use your student loan to get a new car, how to fill out those first day of work tax forms without calling mom and dad,and how to build credit without getting into credit card debt.</p>
  <p>Personal financial skills will keep your wallet full and your options open.Take charge of your finances today!</p>
</div>
<a class="white-btn btn abs" href="#" style="left:145px;top:2027px;width:145px;height:47px">Read more</a>
<div class="checklist-card abs"></div>
<div class="checklist-art abs" role="img" aria-label="Dorm &amp; Done money checklist infographic with nine topic groups of tick-box items, from banking basics to moving up"></div>

<section class="reviews abs"></section>
<h2 class="reviews-title abs">Don’t Take Our Word For It…</h2>
<div class="avatar is-active abs" style="left:197px;top:2356px" role="img" aria-label="Portrait photo of a reviewer"></div>
<div class="avatar abs" style="left:375px;top:2356px" role="img" aria-label="Portrait photo of a reviewer"></div>
<div class="avatar abs" style="left:553px;top:2356px" role="img" aria-label="Portrait photo of a reviewer"></div>
<div class="avatar abs" style="left:731px;top:2356px" role="img" aria-label="Portrait photo of a reviewer"></div>
<div class="avatar abs" style="left:909px;top:2356px" role="img" aria-label="Portrait photo of a reviewer"></div>
<p class="review-quote abs">“Believe it or not, I was fifty before I understood the difference between gross and net profit. Where was Varsity Purse when I needed it?”</p>
<p class="review-author abs">– Rupert Ashby, Founder of Lantern Group</p>

<footer class="site-footer abs"></footer>
<div class="social abs">
  <a class="social-link" href="#" aria-label="Social profile"><i></i></a>
  <a class="social-link" href="#" aria-label="Social profile"><i></i></a>
  <a class="social-link" href="#" aria-label="Photo sharing profile"><i></i></a>
  <a class="social-link" href="#" aria-label="Social profile"><i></i></a>
  <a class="social-link" href="#" aria-label="Favourites">
    <svg width="18" height="16" viewBox="0 0 24 21"><path fill="#fff" d="M12 21l-1.7-1.5C4.2 14 0 10.3 0 6.3 0 2.8 2.7 0 6.2 0 8.1 0 10 .9 12 2.4 14 .9 15.9 0 17.8 0 21.3 0 24 2.8 24 6.3c0 4-4.2 7.7-10.3 13.2z"/></svg>
  </a>
</div>
<nav class="footer-nav abs">
  <ul class="nav-list">
    <li>Home</li><li>Take the pledge</li><li>Blog</li><li>About us</li><li>Tips &amp; tricks</li><li>About nuvoe</li><li>Login</li>
  </ul>
</nav>
<p class="copyright abs">© 2019 Company Name &nbsp;|&nbsp; All rights reserved.</p>

</body>
</html>
```